Luxury WordPress Website for CORALBASINS

I need a professional WordPress website for Coral Basins. The site should be modern, visually appealing, and user-friendly, reflecting the brand’s luxury and premium identity. It must include a homepage, product/service pages, contact form, and be responsive on both desktop and mobile devices. The design should allow for easy updates and integration of future content, while maintaining a polished and professional look.

Target Market(s)

swimmingpool & spa

Industry/Entity Type

Swimmingpool

Coding

Coded - Design and coding required

Font styles to use
Other font styles liked:
• HaboroSoft

Requirements
Must have
• Exclusive appearance
Nice to have
• • A logo that subtly incorporates water or pool elements. • A color palette that reflects luxury, elegance, and relaxation. • Clean and modern typography that is easy to read across all media. • Iconography or design elements that convey premium quality. • A versatile design that can be adapted for social media, merchandise, and promotional materials. • Optional: A tagline that emphasizes luxury and high-end pool experiences.

```html
<!DOCTYPE html>
<html lang="en">
<head>
<meta charset="utf-8">
<title>Coral Basins — Luxury Pools</title>
<link href="https://fonts.googleapis.com/css2?family=Poppins:wght@600;700&family=Roboto:wght@400;500;700&display=swap" rel="stylesheet">
<style>
:root{
  --navy:#0c3a8e;
  --navy-deep:#08307a;
  --teal:#17a8ad;
  --teal-light:#22b9b4;
  --text:#3d4552;
  --muted:#5d6470;
  --water-light:#cfeefa;
  --white:#ffffff;
  --star:#f6a821;
}
*{margin:0;padding:0;box-sizing:border-box}
html,body{width:1200px;height:4360px;overflow:hidden}
body{position:relative;background:var(--white);font-family:'Roboto',Arial,sans-serif;color:var(--text)}
.abs{position:absolute}
h1,h2,.heading{font-family:'Poppins',Arial,sans-serif;font-weight:700}
.accent{color:var(--teal)}
.navy{color:var(--navy)}

/* header */
.site-header{position:absolute;left:0;top:0;width:1200px;height:122px;background:var(--white);z-index:5}
.brand{position:absolute;left:144px;top:26px;display:flex;align-items:center;gap:14px}
.brand-dot{width:76px;height:76px;border-radius:50%;background:linear-gradient(135deg,var(--teal),var(--navy))}
.brand-name{font-family:'Roboto',Arial,sans-serif;font-weight:500;font-size:31px;color:#1c1f26;line-height:1}
.brand-tag{font-size:12px;color:var(--teal);font-weight:500;margin-top:8px;letter-spacing:.2px}
.main-nav{position:absolute;top:52px;left:516px;display:flex;gap:0;font-size:13.5px;font-weight:500;color:#23262c}
.main-nav span{position:absolute;white-space:nowrap}
.main-nav .active{border-bottom:2px solid var(--teal);padding-bottom:4px;color:var(--navy)}
.call-box{position:absolute;left:933px;top:0;width:267px;height:112px;background:linear-gradient(100deg,var(--teal-light),#1185b5 60%,#1365b0)}
.call-icon{position:absolute;left:977px;top:36px;width:48px;height:48px;border-radius:50%;background:var(--navy);z-index:6}
.call-text{position:absolute;left:975px;top:38px;color:#fff;z-index:6;font-weight:500}
.call-text small{display:block;font-size:16px;margin-left:0}
.call-text strong{font-size:21px;font-weight:700}

/* hero */
.hero-photo{position:absolute;left:0;top:122px;width:1200px;height:760px;background:linear-gradient(180deg,#5a8fd0 0%,#2d6b4b 30%,#4f6b3e 48%,#9aa4a4 60%,#34bde0 75%,#8fa09f 100%)}
.hero-circle{position:absolute;left:144px;top:222px;width:464px;height:464px;border-radius:50%;background:#fff;border:6px solid var(--teal);box-shadow:0 0 0 4px #fff;text-align:center;padding-top:84px}
.hero-circle h1{font-size:44px;line-height:52px;color:var(--navy)}
.hero-circle p{font-size:19px;line-height:29px;color:#1d2027;margin-top:18px}
.btn{display:inline-block;background:var(--navy);color:#fff;font-weight:700;font-size:15px;border-radius:30px;text-transform:uppercase}
.hero-circle .btn{margin-top:24px;padding:18px 28px}
.slider-dot{position:absolute;width:36px;height:36px;border-radius:50%}

/* about */
.water-bg{position:absolute;left:0;top:880px;width:1200px;height:1160px;background:linear-gradient(180deg,#fff 0%,#eaf8fd 18%,#bfe9f8 45%,#d9f3fb 62%,#fff 78%)}
.section-title{position:absolute;font-size:44px;color:var(--navy)}
.about-text{position:absolute;left:146px;top:1042px;width:394px;font-size:15.5px;line-height:33px;text-align:justify;color:var(--muted)}
.about-btn{position:absolute;left:146px;top:1329px;width:150px;height:50px;line-height:50px;text-align:center}
.about-image{position:absolute;left:670px;top:985px;width:490px;height:390px;border-radius:48% 52% 46% 54%/50% 44% 56% 50%;border:14px solid #fff;outline:7px solid #4c5259;background:linear-gradient(180deg,#8a6a4a 0%,#b89c7a 22%,#e8e6e2 40%,#1e86d6 70%,#1458b0 100%)}

/* signature */
.card{position:absolute;top:1760px;width:356px;height:540px;border-radius:22px 22px 0 0;text-align:center;color:#fff}
.card-blue{background:var(--navy)}
.card-teal{background:linear-gradient(180deg,var(--teal-light),#149aa5);box-shadow:0 8px 30px rgba(0,0,0,.25)}
.card-photo{position:absolute;top:-108px;left:66px;width:224px;height:224px;border-radius:50%;border:4px solid #fff}
.card h3{position:absolute;top:150px;left:0;width:100%;font-size:20px;font-weight:500}
.card p{position:absolute;top:190px;left:38px;width:280px;font-size:16px;line-height:27px;text-align:justify;text-align-last:center}
.card .more{position:absolute;left:0;width:100%;font-size:13.5px;font-weight:500;text-decoration:underline}

/* why choose */
.feature{position:absolute;width:300px}
.feature h4{font-size:18px;color:var(--navy);font-weight:700}
.feature p{font-size:16.5px;line-height:25px;color:var(--muted);margin-top:14px}
.feature.left{text-align:right}
.feat-icon{position:absolute;width:78px;height:78px;border-radius:50%;border:5px solid #fff;box-shadow:0 3px 10px rgba(0,0,0,.15)}

/* reviews */
.reviews{position:absolute;left:0;top:3000px;width:1200px;height:545px;background:linear-gradient(180deg,#17a8ad,#1bb4b2 50%,#16a2aa)}
.review-photo{position:absolute;left:168px;top:3306px;width:172px;height:172px;border-radius:50%;border:4px solid #fff;background:linear-gradient(160deg,#c98a60,#2b9fc8)}
.review-text{position:absolute;left:421px;top:3300px;width:560px;font-size:15px;line-height:29px;color:#fff}
.review-name{position:absolute;left:421px;top:3403px;color:#fff;font-size:14px;font-weight:700;line-height:22px}
.stars{position:absolute;left:421px;top:3452px;color:var(--star);font-size:18px;letter-spacing:1px}
.quote-mark{position:absolute;font-family:Georgia,serif;font-size:110px;color:rgba(255,255,255,.35);line-height:1}
.nav-circle{position:absolute;width:36px;height:36px;border-radius:50%;border:2px solid rgba(255,255,255,.55)}

/* contact */
.contact{position:absolute;left:0;top:3541px;width:1200px;height:620px;background:radial-gradient(ellipse at 90% 60%,#1b5cb0 0%,var(--navy-deep) 45%,#0a2f79 100%)}
.field{position:absolute;background:#fff;border:1px solid #c9d2de;font-size:13.5px;color:#4a4f57;padding:14px 18px}
.submit{position:absolute;left:525px;top:3980px;width:150px;height:51px;line-height:51px;text-align:center;border-radius:30px;background:var(--teal-light);color:#fff;font-weight:700;font-size:15px}

/* footer */
.social{position:absolute;top:4192px;width:32px;height:32px;border-radius:50%;background:var(--navy)}
.footer-brand{position:absolute;left:736px;top:4240px;display:flex;align-items:center;gap:14px}
.copyright{position:absolute;left:144px;top:4286px;font-size:15px;color:#2b2f36}
</style>
</head>
<body>

<header class="site-header">
  <div class="brand">
    <div class="brand-dot"></div>
    <div>
      <div class="brand-name">Coral Basins</div>
      <div class="brand-tag">ALL YOUR DREAMS COME TRUE</div>
    </div>
  </div>
  <nav class="main-nav">
    <span class="active" style="left:0">HOME</span>
    <span style="left:63px">ABOUT US</span>
    <span style="left:153px">SERVICES</span>
    <span style="left:241px">NEWS</span>
    <span style="left:302px">CONTACT</span>
  </nav>
</header>
<div class="call-box"></div>
<div class="call-icon">
  <svg width="48" height="48" viewBox="0 0 48 48"><path d="M18 15c1-1 2-1 3 0l3 4c.6 1 .4 2-.4 2.6l-1.6 1.2c1 2.4 2.8 4.2 5.2 5.2l1.2-1.6c.6-.8 1.6-1 2.6-.4l4 3c1 1 1 2 0 3l-1.6 1.6c-1.6 1.6-4.4 1.4-8-1.2-3.4-2.4-6.6-5.6-9-9-2.6-3.6-2.8-6.4-1.2-8z" fill="#fff"/></svg>
</div>
<div class="call-text" style="left:975px">
  <small>CALL US</small>
  <strong>+1 555 014 2290</strong>
</div>

<!-- hero -->
<div class="hero-photo" role="img" aria-label="Outdoor pool with stone deck, white parasols and loungers in front of pine trees"></div>
<svg class="abs" style="left:0;top:680px" width="1200" height="220" viewBox="0 0 1200 220">
  <path d="M0 130 C200 200 420 150 620 80 C820 10 1000 30 1200 110 L1200 220 L0 220Z" fill="#fff"/>
  <path d="M0 140 C220 220 440 150 640 80 C830 20 1000 40 1180 105" fill="none" stroke="var(--teal)" stroke-width="6"/>
  <path d="M0 118 C200 175 420 120 620 60 C800 10 960 20 1100 60" fill="none" stroke="var(--navy)" stroke-width="10"/>
  <path d="M0 170 C240 230 460 170 680 100 C860 50 1020 60 1200 120" fill="none" stroke="#1b6fb8" stroke-width="14" opacity=".9"/>
</svg>
<div class="hero-circle">
  <h1>Luxury Pools.<br><span class="accent">Crafted for a</span><br>Lifetime</h1>
  <p>Exclusive custom pools that redefine<br>design, durability, and relaxation.</p>
  <span class="btn">Explore our designs</span>
</div>
<div class="slider-dot" style="left:1054px;top:707px;background:var(--teal)">
  <svg width="36" height="36"><path d="M21 12l-6 6 6 6" stroke="#fff" stroke-width="3" fill="none"/></svg></div>
<div class="slider-dot" style="left:1094px;top:713px;background:var(--navy)">
  <svg width="36" height="36"><path d="M15 12l6 6-6 6" stroke="#fff" stroke-width="3" fill="none"/></svg></div>

<!-- about -->
<div class="water-bg"></div>
<h2 class="section-title" style="left:146px;top:958px">About <span class="accent">Us</span></h2>
<p class="about-text">Sed ut perspiciatis unde omnis iste natus error sit voluptatem accusantium doloremque laudantium, totam rem aperiam, eaque ipsa quae ab illo inventore veritatis et quasi architecto beatae vitae dicta sunt explicabo. Nemo enim ipsam voluptatem quia voluptas sit aspernatur aut odit aut fugit, sed quia consequuntur magni dolores eos qui ratione voluptatem sequi nesciunorrm quia dolor sit amconsectetu.</p>
<span class="btn about-btn">Read more</span>
<div class="about-image" role="img" aria-label="Indoor pool hall with wooden slatted ceiling, framed in a kidney-shaped pool outline"></div>

<!-- signature collection -->
<h2 class="section-title" style="left:0;width:1200px;text-align:center;top:1537px">Our Signature <span class="accent">Collection</span></h2>
<div class="card card-blue" style="left:41px">
  <div class="card-photo" role="img" aria-label="Swimmer relaxing at the edge of an infinity pool overlooking the sea" style="background:linear-gradient(180deg,#3f7fc4,#1b4f9a)"></div>
  <h3>Infinity Edge Pools</h3>
  <p>Sed ut perspiciatis unde omnis iste natus error sit voluptatem cusantium doloremque</p>
  <span class="more" style="top:295px">READ MORE</span>
</div>
<div class="card card-teal" style="left:423px">
  <div class="card-photo" role="img" aria-label="Modern architectural villa with pool and sun loungers by the ocean" style="background:linear-gradient(180deg,#8dc7ee,#e9e6e0 60%,#a88f75)"></div>
  <h3>Architectural Pools</h3>
  <p>Sed ut perspiciatis unde omnis iste natus error sit voluptatem cusantium doloremqed ut perspiciatis unde omnis iste natus error sit voluptatem cusantium doloremque</p>
  <span class="more" style="top:350px">READ MORE</span>
</div>
<div class="card card-blue" style="left:804px">
  <div class="card-photo" role="img" aria-label="Guest enjoying a water cascade in a wellness spa pool" style="background:linear-gradient(180deg,#dfeff3,#2db2c6)"></div>
  <h3>Wellness &amp; Spa Pools</h3>
  <p>Sed ut perspiciatis unde omnis iste natus error sit voluptatem cusantium doloremqed ut perspiciatis unde omnis iste natus error sit voluptatem cusantium doloremque</p>
  <span class="more" style="top:360px">READ MORE</span>
</div>
<svg class="abs" style="left:0;top:2090px" width="1200" height="250" viewBox="0 0 1200 250">
  <path d="M0 90 C180 30 380 20 560 90 C740 160 900 200 1200 110 L1200 250 L0 250Z" fill="#fff"/>
  <path d="M0 100 C180 30 380 10 580 90 C760 160 920 200 1120 140" fill="none" stroke="var(--teal)" stroke-width="8"/>
  <path d="M80 90 C260 40 420 50 600 120 C780 190 940 210 1200 120" fill="none" stroke="var(--navy)" stroke-width="9"/>
</svg>

<!-- why choose -->
<h2 class="section-title" style="left:0;width:1200px;text-align:center;top:2355px">Why Choose <span class="accent">Coral Basins</span></h2>
<div class="feature left" style="left:115px;top:2532px"><h4>Unmatched Craftsmanship</h4><p>Built with precision, using only the<br>finest materials.</p></div>
<div class="feature left" style="left:115px;top:2756px"><h4>Engineered for Durability</h4><p>Designed to last a lifetime.</p></div>
<div class="feature" style="left:786px;top:2532px"><h4>Innovative Design</h4><p>Seamlessly blending form and<br>function.</p></div>
<div class="feature" style="left:786px;top:2756px"><h4>Luxury Experience</h4><p>From concept to completion, we<br>deliver perfection.</p></div>
<svg class="abs" style="left:431px;top:2518px" width="340" height="340" viewBox="0 0 340 340">
  <circle cx="170" cy="170" r="160" fill="none" stroke="#d5dde6" stroke-width="3"/>
  <circle cx="170" cy="170" r="145" fill="none" stroke="#e5ebf1" stroke-width="2"/>
  <path d="M110 18 A160 160 0 0 1 230 18" fill="none" stroke="var(--teal)" stroke-width="4"/>
  <path d="M110 322 A160 160 0 0 0 230 322" fill="none" stroke="var(--teal)" stroke-width="4"/>
  <circle cx="170" cy="170" r="112" fill="#fff"/>
</svg>
<div class="abs" role="img" aria-label="Garden pool with loungers surrounded by hedges and trees" style="left:493px;top:2580px;width:216px;height:216px;border-radius:50%;background:linear-gradient(180deg,#e9b7a8 0%,#4f7a3e 40%,#2e9fd4 70%,#6aa04a 100%)"></div>
<div class="feat-icon" style="left:445px;top:2532px;background:var(--navy)">
  <svg width="68" height="68"><g stroke="#fff" stroke-width="3" fill="none"><path d="M20 28q4-4 7 0t7 0 7 0 7 0"/><path d="M20 35q4-4 7 0t7 0 7 0 7 0"/><path d="M20 42q4-4 7 0t7 0 7 0 7 0"/></g></svg></div>
<div class="feat-icon" style="left:670px;top:2532px;background:var(--teal)">
  <svg width="68" height="68"><path d="M25 20h13l7 7v21H25z" fill="#fff"/></svg></div>
<div class="feat-icon" style="left:445px;top:2756px;background:var(--teal)">
  <svg width="68" height="68"><circle cx="34" cy="34" r="13" fill="#fff"/><path d="M34 27v8h6" stroke="var(--teal)" stroke-width="3" fill="none"/></svg></div>
<div class="feat-icon" style="left:670px;top:2756px;background:var(--navy)">
  <svg width="68" height="68"><path d="M23 34l8 8 14-15" stroke="#fff" stroke-width="5" fill="none"/></svg></div>

<!-- reviews -->
<div class="reviews"></div>
<svg class="abs" style="left:0;top:2930px" width="1200" height="200" viewBox="0 0 1200 200">
  <path d="M0 0 L1200 0 L1200 80 C1050 10 880 10 720 70 C560 130 420 170 200 150 C110 140 40 120 0 100Z" fill="#d6f1fa"/>
  <path d="M0 100 C60 140 140 160 240 158 C430 155 560 110 720 60 C880 10 1050 20 1200 90" fill="none" stroke="var(--navy)" stroke-width="16"/>
  <path d="M0 120 C80 150 160 168 260 165" fill="none" stroke="#fff" stroke-width="4"/>
</svg>
<h2 class="heading abs" style="left:0;width:1200px;text-align:center;top:3187px;font-size:44px;color:#fff">Customer Reviews</h2>
<div class="nav-circle" style="left:91px;top:3373px"><svg width="32" height="32"><path d="M19 9l-7 7 7 7" stroke="rgba(255,255,255,.7)" stroke-width="2" fill="none"/></svg></div>
<div class="nav-circle" style="left:1073px;top:3373px"><svg width="32" height="32"><path d="M13 9l7 7-7 7" stroke="rgba(255,255,255,.7)" stroke-width="2" fill="none"/></svg></div>
<div class="review-photo" role="img" aria-label="Smiling mother and daughter in a pool"></div>
<span class="quote-mark" style="left:348px;top:3290px">“</span>
<span class="quote-mark" style="left:910px;top:3420px">”</span>
<p class="review-text">“Sed ut perspiciatis unde omnis iste natus error sit voluptatem accusantium doloremque laudantium, totam rem aperiam, eaque ipsa quae ab illo inventore veritatis et architectoquasi archititae dicta arco enim ipsarchitectoa”</p>
<div class="review-name">- MARA ELLISON<br>LOREM IPSUM DOLOR SIT AMET</div>
<div class="stars">★★★★★</div>

<!-- contact -->
<div class="contact" role="img" aria-label="Deep blue water background with a relaxing swimmer"></div>
<h2 class="heading abs" style="left:0;width:1200px;text-align:center;top:3630px;font-size:44px;color:#fff">Contact <span class="accent">Us</span></h2>
<div class="field" style="left:215px;top:3729px;width:372px;height:44px">First Name</div>
<div class="field" style="left:611px;top:3729px;width:374px;height:44px">Last Name</div>
<div class="field" style="left:215px;top:3797px;width:372px;height:44px">Email Address</div>
<div class="field" style="left:611px;top:3797px;width:374px;height:44px">Phone</div>
<div class="field" style="left:215px;top:3866px;width:770px;height:83px">Message</div>
<div class="submit">SUBMIT</div>

<!-- footer -->
<svg class="abs" style="left:0;top:4080px" width="1200" height="280" viewBox="0 0 1200 280">
  <path d="M0 90 C200 180 420 150 620 80 C820 20 1000 10 1200 60 L1200 280 L0 280Z" fill="#fff"/>
  <path d="M0 80 C220 160 430 130 620 70 C820 10 1000 0 1200 40" fill="none" stroke="var(--navy)" stroke-width="12"/>
  <path d="M0 100 C220 190 440 150 640 90 C840 30 1010 30 1200 70" fill="none" stroke="var(--teal)" stroke-width="5"/>
</svg>
<div class="social" style="left:836px" aria-label="Social profile"></div>
<div class="social" style="left:876px" aria-label="Social profile"></div>
<div class="social" style="left:916px;background:#fff;border:2px solid var(--navy)" aria-label="Social profile"></div>
<div class="social" style="left:956px" aria-label="Social profile"></div>
<div class="social" style="left:996px" aria-label="Social profile"></div>
<div class="footer-brand">
  <div class="brand-dot" style="width:72px;height:72px"></div>
  <div>
    <div class="brand-name">Coral Basins</div>
    <div class="brand-tag">ALL YOUR DREAMS COME TRUE</div>
  </div>
</div>
<p class="copyright">© 2025 Companyname.All Rights Reserved &nbsp;|&nbsp; Privacy Policy &nbsp;|&nbsp; Terms of use</p>

</body>
</html>
```